-Photo booth rental Web Design Project

Our business is a small photo booth rental service serving the capital region and surrounding areas. The photo booth is a portable booth that fits up to 10 guest. I am looking for a website that will have social media capabilities and also private log ins for clients to view their photo albums online after their event. We provide full service photo booth rentals for all types of parties. I am looking for something fun and unique but also professional and I am also looking to maybe somehow incorporate the age of the photo booth which was invented in 1888. I do not have the photos of our photo booth available because we are just starting up and I wanted to get everything together first but I will provide stock photo booth pictures .Thank you for your patience i know it wont be an easy task with out those things. I added a word document describing information i will need on our website, i am looking for a home page, contact us and book an event page, online gallery page, and pricing. If you need any more information please feel free to contact me. Thanks for your help and I look forward to working with you.

Target Market(s)

For everyone from brides to be for their weddings or private parties, corporate parties, school dances, charity events, community events ect

Industry/Entity Type

Business

Requirements
Nice to have
• social media sharing

```html
<!DOCTYPE html>
<html lang="en">
<head>
<meta charset="utf-8">
<title>Giggle Frame Photo Booth</title>
<link rel="stylesheet" href="https://fonts.googleapis.com/css2?family=Oswald:wght@400;500&family=Open+Sans:wght@400;600&family=Roboto:wght@400&display=swap">
<style>
  :root {
    --brown: #3d2519;
    --brown-mid: #6b3a26;
    --red: #d9342b;
    --ink: #333333;
    --muted: #777777;
    --line: #e6e6e6;
    --paper: #ffffff;
    --footer: #f1f1f1;
  }
  * { margin: 0; padding: 0; box-sizing: border-box; }
  html, body { width: 820px; height: 1200px; overflow: hidden; background: var(--paper); }
  body { position: relative; font-family: "Open Sans", sans-serif; color: var(--ink); }
  .abs { position: absolute; }

  /* header */
  .brand { left: 117px; top: 24px; font-family: "Open Sans", sans-serif; font-weight: 600; font-size: 28px; line-height: 1; color: var(--brown); }
  .brand-dot { left: 292px; top: 28px; width: 22px; height: 22px; border-radius: 50%; background: var(--brown); }
  .nav { top: 38px; left: 379px; display: flex; gap: 0; font-size: 10px; color: #555; }
  .nav a { color: inherit; text-decoration: none; position: absolute; white-space: nowrap; }
  .nav a.active { color: var(--brown-mid); }

  /* hero */
  .hero-band { left: 0; top: 84px; width: 820px; height: 280px; background: var(--brown); }
  .hero-photo { left: 117px; top: 84px; width: 586px; height: 318px;
    background: linear-gradient(100deg, #8d8d8b 0%, #b3b2ad 35%, #a09c95 60%, #6e6a63 100%);
    box-shadow: 0 6px 8px -6px rgba(0,0,0,.35); }
  .hero-title { left: 117px; width: 586px; text-align: center; font-family: "Oswald", sans-serif; color: #fff; text-shadow: 0 2px 4px rgba(0,0,0,.35); }
  .hero-title.main { top: 164px; font-size: 38px; font-weight: 500; }
  .hero-title.sub { top: 222px; font-size: 27px; font-weight: 400; }
  .btn-hero { left: 340px; top: 277px; width: 139px; height: 29px; border-radius: 15px; background: var(--red); color: #fff;
    font-family: "Oswald", sans-serif; font-size: 11.5px; display: flex; align-items: center; justify-content: center; }
  .dots { left: 385px; top: 327px; display: flex; gap: 5px; }
  .dots span { width: 7px; height: 7px; border-radius: 50%; background: #fff; }
  .dots span.on { background: var(--red); box-shadow: 0 0 0 2px rgba(255,255,255,.4); }

  /* welcome */
  .booth-photo { left: 119px; top: 422px; width: 133px; height: 178px; background: linear-gradient(90deg, #1c1c1c, #8a1f1f 45%, #1c1c1c); }
  .welcome-kicker { left: 282px; top: 423px; font-family: "Roboto", sans-serif; font-size: 22px; color: #444; }
  .welcome-title { left: 282px; top: 452px; font-family: "Roboto", sans-serif; font-size: 18px; color: var(--brown-mid); }
  .welcome-copy { left: 282px; top: 488px; width: 420px; font-size: 7.2px; line-height: 13.4px; color: var(--muted); }
  .btn-gallery { left: 282px; top: 569px; width: 69px; height: 24px; background: var(--red); color: #fff; font-size: 8px; border-radius: 2px;
    display: flex; align-items: center; justify-content: center; }

  /* pricing */
  .pricing-bg { left: 0; top: 620px; width: 820px; height: 370px; background: linear-gradient(180deg, #f4f4f4, #ebebeb 70%, #f2f2f2); }
  .plan { top: 648px; width: 181px; height: 313px; background: #fafafa; box-shadow: 0 1px 2px rgba(0,0,0,.08); }
  .plan-head { height: 32px; background: var(--brown); color: #fff; font-family: "Oswald", sans-serif; font-size: 11px; letter-spacing: .2px;
    display: flex; align-items: center; justify-content: center; }
  .price { width: 84px; height: 84px; margin: 13px auto 15px; border-radius: 50%; background: var(--brown-mid); color: #fff; text-align: center; padding-top: 17px; }
  .plan.extreme .price { background: var(--red); }
  .price b { display: block; font-weight: 400; font-size: 20px; line-height: 1; }
  .price small { display: block; font-size: 6.4px; line-height: 13px; margin-top: 3px; }
  .features { list-style: none; }
  .features li { height: 24.6px; border-top: 1px solid var(--line); font-size: 6.8px; color: #666; display: flex; align-items: center; justify-content: center; }

  /* promo */
  .promo-line { left: 0; width: 820px; text-align: center; font-family: "Oswald", sans-serif; }
  .promo-line.top { top: 1014px; font-size: 21px; color: var(--brown-mid); letter-spacing: -.3px; }
  .promo-line.big { top: 1046px; font-size: 36px; color: var(--red); font-weight: 500; }

  /* footer */
  .footer { left: 0; top: 1125px; width: 820px; height: 75px; background: var(--footer); }
  .copyright { left: 118px; top: 1144px; font-size: 8px; color: #444; }
  .foot-links { left: 118px; top: 1167px; font-size: 8px; color: #444; white-space: nowrap; }
  .social { left: 397px; top: 1154px; display: flex; gap: 4px; }
  .social span { width: 18px; height: 18px; border-radius: 50%; }
  .newsletter { left: 516px; top: 1138px; font-size: 10px; color: var(--red); }
  .email { left: 516px; top: 1160px; width: 127px; height: 21px; border: 1px solid #ddd; background: #fff; font-size: 6.8px; color: #888; padding: 6px 9px; }
  .btn-sub { left: 650px; top: 1160px; width: 53px; height: 21px; background: var(--red); color: #fff; font-size: 8px; border-radius: 2px;
    display: flex; align-items: center; justify-content: center; }
</style>
</head>
<body>

<header>
  <div class="abs brand">Giggle Frame</div>
  <div class="abs brand-dot"></div>
  <nav class="abs nav">
    <a class="active" style="left:0">HOME</a>
    <a style="left:53px">PRICING</a>
    <a style="left:114px">BOOK AN EVENT</a>
    <a style="left:211px">CLIENT</a>
    <a style="left:268px">CONTACT US</a>
  </nav>
</header>

<section class="hero">
  <div class="abs hero-band"></div>
  <div class="abs hero-photo" role="img" aria-label="Photo of a photographer holding a camera with a large lens"></div>
  <h1 class="abs hero-title main">GIGGLE FRAME</h1>
  <h2 class="abs hero-title sub">PHOTO BOOTH RENTAL COMPANY</h2>
  <div class="abs btn-hero">BOOK AN EVENT</div>
  <div class="abs dots"><span class="on"></span><span></span><span></span><span></span></div>
</section>

<section class="welcome">
  <div class="abs booth-photo" role="img" aria-label="Photo of a couple standing beside a portable photo booth"></div>
  <p class="abs welcome-kicker">Welcome To</p>
  <h2 class="abs welcome-title">Giggle Frame Photo Booth</h2>
  <p class="abs welcome-copy">Our Booths feature the latest equipment and technology with SmartTouch screens, social and email uploading, MP3 player ready speaker systems, and dual "Photo Booth" or "Video Booth" modes with 1080p HD<br>Fun entertainment &amp; favors for all event types, ex: weddings, birthday parties, graduations, holiday parties, corporate parties, bar/ bat mitzvahs, bridal showers, baby showers, anniversaries, grand openings, school events, proms, corporate events, promotional events, trade shows, conventions, community &amp; charity events</p>
  <div class="abs btn-gallery">View Gallery</div>
</section>

<section class="pricing">
  <div class="abs pricing-bg" role="img" aria-label="Faint photo of a city skyline"></div>

  <div class="abs plan" style="left:117px">
    <div class="plan-head">STANDARD PLAN</div>
    <div class="price"><b>$675</b><small>DIGITAL<br>BACKDROP</small></div>
    <ul class="features">
      <li>3 HOURS OF SERVICE</li><li>SET UP &amp; REMOVAL</li><li>PROFESSIONAL &amp; FRIENDLY BOOTH</li>
      <li>DVD OR USB FLASH DRIVE OF PICTURE</li><li>GUESTBOOK</li><li>UNLIMITED PRINTS</li><li>ONLINE GALLERY</li>
    </ul>
  </div>

  <div class="abs plan" style="left:321px">
    <div class="plan-head">ULTIMATE PLAN</div>
    <div class="price"><b>$850</b><small>DIGITAL<br>BACKDROP</small></div>
    <ul class="features">
      <li>3 HOURS OF SERVICE</li><li>SET UP &amp; REMOVAL</li><li>PROFESSIONAL &amp; FRIENDLY BOOTH</li>
      <li>DVD OR USB FLASH DRIVE OF PICTURE</li><li>GUESTBOOK</li><li>UNLIMITED PRINTS</li><li>ONLINE GALLERY</li>
    </ul>
  </div>

  <div class="abs plan extreme" style="left:522px">
    <div class="plan-head">EXTREME PLAN</div>
    <div class="price"><b>$975</b><small>DIGITAL<br>BACKDROP</small></div>
    <ul class="features">
      <li>3 HOURS OF SERVICE</li><li>SET UP &amp; REMOVAL</li><li>PROFESSIONAL &amp; FRIENDLY BOOTH</li>
      <li>DVD OR USB FLASH DRIVE OF PICTURE</li><li>GUESTBOOK</li><li>UNLIMITED PRINTS</li><li>ONLINE GALLERY</li>
    </ul>
  </div>
</section>

<section class="promo">
  <p class="abs promo-line top">MAGNET PHOTO STRIP FRAMES, STAND UP ACRYLIC PHOTO STRIP FRAMES,</p>
  <p class="abs promo-line big">ONLY $100 DEPOSIT</p>
</section>

<footer>
  <div class="abs footer"></div>
  <p class="abs copyright">©2014 Giggle Frame , All Rights Reserved.</p>
  <p class="abs foot-links">Home &nbsp;| &nbsp;Pricing &nbsp;| &nbsp;book an event &nbsp;| &nbsp;Client | &nbsp;Contact Us</p>
  <div class="abs social"><span style="background:#3b5a98"></span><span style="background:#2aa3d8"></span><span style="background:#cf2a27"></span></div>
  <p class="abs newsletter">Newsletter Sign Up</p>
  <div class="abs email">Enter Your Email</div>
  <div class="abs btn-sub">Subscribe</div>
</footer>

</body>
</html>
```